Casa Morellina Togo Menu seperated in categories

new to go menu for italian restaurant with menu descriptions and prices i like the cover first page to have all the restaurant information, the other pages should be separated in the menu categories, and if we can include a map with the location of the restaurant
Casa Morellina
42 Route 83 S
North Myrtle Beach, SC 29582
open 7 days a week 4-10
Happy hour served Daily at the Bar 4-7
www.casamorellina.com
casamorellinadine@maildrop.example

Restaurant

Sans Serif

Must have
• Prices and pictures and restaurant information

```html
<!DOCTYPE html>
<html lang="en">
<head>
<meta charset="utf-8">
<title>Casa Morellina – Pollo &amp; Vitello</title>
<link rel="stylesheet" href="https://fonts.googleapis.com/css2?family=Questrial&family=Montserrat:wght@700&display=swap">
<style>
  :root {
    --backdrop: #cd8c5e;
    --panel: #f2f4f5;
    --green: #3b8475;
    --crimson: #b8124a;
    --white: #ffffff;
    --ink: #1a1a1a;
    --emblem: #f5e0a3;
  }
  html, body {
    margin: 0;
    padding: 0;
    width: 849px;
    height: 1200px;
    overflow: hidden;
    background: var(--backdrop);
  }
  .page {
    position: relative;
    width: 827px;
    height: 1169px;
    transform: scale(1.02661);
    transform-origin: 0 0;
    font-family: "Questrial", sans-serif;
    color: var(--ink);
  }
  .frame {
    position: absolute;
    inset: 0;
  }
  .emblem-name {
    position: absolute;
    left: 105px;
    width: 617px;
    top: 520px;
    text-align: center;
    font-family: "Questrial", sans-serif;
    font-size: 58px;
    color: var(--emblem);
    letter-spacing: 1px;
  }
  .intro {
    position: absolute;
    left: 118px;
    top: 115px;
    width: 592px;
    color: var(--green);
    font-size: 15.5px;
    line-height: 21px;
  }
  .section-title {
    margin: 0 0 4px;
    font-family: "Montserrat", sans-serif;
    font-weight: 700;
    font-size: 19px;
    letter-spacing: 0.3px;
  }
  .intro p { margin: 0; text-align: justify; }
  .dish {
    position: absolute;
    left: 118px;
    width: 592px;
    font-size: 15.5px;
    line-height: 21px;
  }
  .dish-name {
    margin: 0 0 2px;
    color: var(--crimson);
    font-weight: 400;
    font-size: 18px;
  }
  .dish-desc { margin: 0; text-align: justify; }
  .prices { list-style: none; margin: 0; padding: 0; }
  .dish--parmigiana { top: 260px; }
  .dish--picatta { top: 402px; }
  .dish--marsala { top: 527px; }
  .dish-photo {
    position: absolute;
    left: 0;
    top: 0;
  }
</style>
</head>
<body>
<div class="page">
  <svg class="frame" width="827" height="1169" viewBox="0 0 827 1169" aria-hidden="true">
    <defs>
      <pattern id="tabs-top" x="105" y="0" width="103" height="1169" patternUnits="userSpaceOnUse">
        <rect x="0" y="48" width="34.3" height="80" rx="17" fill="var(--green)"/>
        <rect x="34.3" y="48" width="34.3" height="80" rx="17" fill="var(--white)"/>
        <rect x="68.6" y="48" width="34.3" height="80" rx="17" fill="var(--crimson)"/>
      </pattern>
      <pattern id="tabs-bottom" x="105" y="0" width="103" height="1169" patternUnits="userSpaceOnUse">
        <rect x="0" y="1040" width="34.3" height="80" rx="17" fill="var(--green)"/>
        <rect x="34.3" y="1040" width="34.3" height="80" rx="17" fill="var(--white)"/>
        <rect x="68.6" y="1040" width="34.3" height="80" rx="17" fill="var(--crimson)"/>
      </pattern>
      <pattern id="tabs-left" x="0" y="95" width="827" height="105" patternUnits="userSpaceOnUse">
        <rect x="57" y="0" width="80" height="35" rx="17" fill="var(--crimson)"/>
        <rect x="57" y="35" width="80" height="35" rx="17" fill="var(--white)"/>
        <rect x="57" y="70" width="80" height="35" rx="17" fill="var(--green)"/>
      </pattern>
      <pattern id="tabs-right" x="0" y="95" width="827" height="105" patternUnits="userSpaceOnUse">
        <rect x="690" y="0" width="80" height="35" rx="17" fill="var(--green)"/>
        <rect x="690" y="35" width="80" height="35" rx="17" fill="var(--white)"/>
        <rect x="690" y="70" width="80" height="35" rx="17" fill="var(--crimson)"/>
      </pattern>
      <linearGradient id="photo-tones" x1="0" y1="0" x2="0.3" y2="1">
        <stop offset="0" stop-color="#4a2a1a"/>
        <stop offset="0.45" stop-color="#8a4a2a"/>
        <stop offset="0.7" stop-color="#d9c7b4"/>
        <stop offset="1" stop-color="#b9a08a"/>
      </linearGradient>
    </defs>
    <rect x="105" y="48" width="617" height="60" fill="url(#tabs-top)"/>
    <rect x="105" y="1060" width="617" height="60" fill="url(#tabs-bottom)"/>
    <rect x="57" y="95" width="60" height="980" fill="url(#tabs-left)"/>
    <rect x="710" y="95" width="60" height="980" fill="url(#tabs-right)"/>
    <rect class="panel" x="105" y="95" width="617" height="980" fill="var(--panel)"/>
  </svg>

  <div class="emblem-name">Casa Morellina</div>

  <header class="intro">
    <h1 class="section-title">POLLO &amp; VITELLO</h1>
    <p>All of our Chicken &amp; Veal Dishes served with fresh baked bread and our roasted red pepper, garlic and herb dipping oil, your choice of soup of the day or house salad, upgrade to Caesar Salad 1.95.<br>Split Entrée includes additional soup or salad 7.00</p>
  </header>

  <section class="dish dish--parmigiana">
    <h2 class="dish-name">Parmigiana</h2>
    <p class="dish-desc">Hand breaded, lightly fried, and topped with our Marinara sauce and fresh Mozzarella, baked to perfection, served over spaghetti</p>
    <ul class="prices">
      <li>Eggplant 15.95</li>
      <li>Chicken 18.95</li>
      <li>Veal 20.95</li>
    </ul>
  </section>

  <section class="dish dish--picatta">
    <h2 class="dish-name">Picatta</h2>
    <p class="dish-desc">Sautéed in a chardonnay lemon butter sauce with Capers, Artichoke hearts and Garlic, served over penne pasta</p>
    <ul class="prices">
      <li>Chicken 18.95</li>
      <li>Veal 21.95</li>
    </ul>
  </section>

  <section class="dish dish--marsala">
    <h2 class="dish-name">Marsala</h2>
    <p class="dish-desc">Sautéed with Mushrooms in a fine Sicilian dry Marsala wine, served over penne pasta</p>
    <ul class="prices">
      <li>Chicken 18.95</li>
      <li>Veal 21.95</li>
    </ul>
  </section>

  <svg class="dish-photo" width="827" height="1169" viewBox="0 0 827 1169">
    <ellipse cx="393" cy="775" rx="212" ry="95" fill="var(--crimson)"/>
    <ellipse cx="435" cy="840" rx="228" ry="135" fill="url(#photo-tones)" role="img" aria-label="Photo of a plated pasta dish with toasted bread and a glass of white wine on a restaurant table"/>
  </svg>
</div>
</body>
</html>
```